Accounting business needs business card

I have a business card but need something better. I want the colour changed and the design to be better. I have uploaded a picture of my new sign that is grey in colour, i would like to incorporate these colours.

```html
<!DOCTYPE html>
<html lang="en">
<head>
<meta charset="utf-8">
<title>Orbit Tax – Business Card</title>
<link href="https://fonts.googleapis.com/css2?family=Montserrat:wght@400;500;700&display=swap" rel="stylesheet">
<style>
  :root {
    --page-bg: #eeeff2;
    --card-white: #ffffff;
    --ink: #2b2b2f;
    --brand-blue: #4a77c4;
    --back-blue-light: #6294d2;
    --back-blue-dark: #4a72bb;
    --faint-line: #e6e7ea;
    --badge-blue: #1d5fb0;
    --partner-cyan: #1ab4e6;
  }
  html, body {
    margin: 0;
    width: 1200px;
    height: 800px;
    overflow: hidden;
    background: var(--page-bg);
    font-family: "Montserrat", sans-serif;
  }
  .canvas {
    position: relative;
    width: 1200px;
    height: 800px;
  }
  .card {
    position: absolute;
    top: 270px;
    width: 470px;
    height: 260px;
    overflow: hidden;
    box-shadow: 0 14px 30px rgba(0,0,0,0.22);
  }
  .card--front { left: 100px; background: var(--card-white); color: var(--ink); }
  .card--back {
    left: 630px;
    background: linear-gradient(100deg, var(--back-blue-dark) 0%, var(--back-blue-light) 40%, var(--back-blue-dark) 75%);
  }
  .card__decor {
    position: absolute;
    inset: 0;
    width: 100%;
    height: 100%;
  }
  .wordmark {
    position: absolute;
    left: 18px;
    top: 14px;
    margin: 0;
    font-weight: 500;
    font-size: 22px;
    letter-spacing: 0.5em;
    color: var(--ink);
  }
  .person {
    position: absolute;
    left: 18px;
    top: 66px;
  }
  .person__name {
    margin: 0;
    font-weight: 700;
    font-size: 18px;
    color: var(--brand-blue);
    line-height: 1.1;
  }
  .person__role {
    margin: 2px 0 0;
    font-size: 11px;
    line-height: 1.4;
  }
  .contacts {
    position: absolute;
    left: 18px;
    top: 136px;
    margin: 0;
    padding: 0;
    list-style: none;
    font-size: 11.5px;
  }
  .contacts li {
    display: flex;
    align-items: center;
    gap: 8px;
    height: 16px;
  }
  .contacts svg { width: 11px; height: 11px; flex: none; }
  .affiliations {
    position: absolute;
    left: 18px;
    top: 205px;
    display: flex;
    align-items: center;
    gap: 7px;
  }
  .affiliations__badge {
    width: 77px;
    height: 33px;
    background: var(--badge-blue);
  }
  .affiliations__note {
    font-size: 9.5px;
    line-height: 1.15;
    width: 75px;
  }
  .affiliations__partner {
    width: 38px;
    height: 38px;
    border-radius: 50%;
    background: var(--partner-cyan);
  }
  .front__rule {
    position: absolute;
    left: 18px;
    top: 254px;
    width: 201px;
    height: 3px;
    background: var(--brand-blue);
  }
  .back__brand {
    position: absolute;
    left: 0;
    right: 0;
    top: 68px;
    display: flex;
    flex-direction: column;
    align-items: center;
    margin-left: 150px;
  }
  .back__circle {
    width: 78px;
    height: 78px;
    border: 2.5px solid #fff;
    border-radius: 50%;
    box-sizing: border-box;
  }
  .back__name {
    margin: 18px 0 0;
    color: #fff;
    font-weight: 500;
    font-size: 24px;
    letter-spacing: 0.5em;
    margin-right: -0.5em;
  }
</style>
</head>
<body>
<main class="canvas">
  <section class="card card--front" aria-label="Card front">
    <svg class="card__decor" viewBox="0 0 470 260" aria-hidden="true">
      <circle cx="443" cy="130" r="131" fill="none" stroke="var(--faint-line)" stroke-width="3"/>
    </svg>
    <h1 class="wordmark">ORBIT TAX</h1>
    <div class="person">
      <p class="person__name">Owen Hartley</p>
      <p class="person__role">CTQ, MTAX, BCOM (Acc &amp; Fin)<br>Taxation and Business Accountant</p>
    </div>
    <ul class="contacts">
      <li>
        <svg viewBox="0 0 12 12"><path d="M2.5 1 L4.5 1 L5.3 3.4 L4 4.4 Q5 6.8 7.6 8 L8.6 6.7 L11 7.5 L11 9.5 Q10.5 11 9 11 Q1 10 1 2.8 Q1 1.5 2.5 1 Z" fill="none" stroke="var(--brand-blue)" stroke-width="1"/></svg>
        0412 555 019
      </li>
      <li>
        <svg viewBox="0 0 12 12"><rect x="0.8" y="2.3" width="10.4" height="7.4" fill="none" stroke="var(--brand-blue)" stroke-width="1"/><path d="M0.8 2.5 L6 6.5 L11.2 2.5" fill="none" stroke="var(--brand-blue)" stroke-width="1"/></svg>
        owen@orbittax.com.au
      </li>
      <li>
        <svg viewBox="0 0 12 12"><circle cx="6" cy="6" r="5" fill="none" stroke="var(--brand-blue)" stroke-width="1"/><ellipse cx="6" cy="6" rx="2.2" ry="5" fill="none" stroke="var(--brand-blue)" stroke-width="0.9"/><path d="M1 6 H11 M1.8 3.5 H10.2 M1.8 8.5 H10.2" stroke="var(--brand-blue)" stroke-width="0.9"/></svg>
        www.orbittax.com.au
      </li>
    </ul>
    <div class="affiliations">
      <div class="affiliations__badge" aria-hidden="true"></div>
      <p class="affiliations__note">Orbit Tax is a<br>Member Practice</p>
      <div class="affiliations__partner" aria-hidden="true"></div>
    </div>
    <div class="front__rule"></div>
  </section>

  <section class="card card--back" aria-label="Card back">
    <svg class="card__decor" viewBox="0 0 470 260" aria-hidden="true">
      <circle cx="66" cy="130" r="131" fill="none" stroke="rgba(255,255,255,0.12)" stroke-width="3"/>
    </svg>
    <div class="back__brand">
      <div class="back__circle" aria-hidden="true"></div>
      <p class="back__name">ORBIT TAX</p>
    </div>
  </section>
</main>
</body>
</html>
```